Birchline Septic Solutions

Would like to see some single sided ones but would also like to see some double sided with one sided only being the logo. Owners name is Colin Vandro. Phone number is 555-214-0387
Services are pumping, inspections, installs, and repairs

Contact Information for Business Card

555-241-0387 Colin Vandro Alderbrook, OH

```html
<!DOCTYPE html>
<html lang="en">
<head>
<meta charset="utf-8">
<title>Birchline Septic Solutions – Business Cards</title>
<link href="https://fonts.googleapis.com/css2?family=Montserrat:wght@500;600;700&display=swap" rel="stylesheet">
<style>
  :root {
    --backdrop: #9a9a9a;
    --ink: #000000;
    --paper: #ffffff;
    --teal: #2bbcb8;
    --rule: #555555;
    --shadow: rgba(0,0,0,0.35);
  }
  * { margin: 0; padding: 0; box-sizing: border-box; }
  html, body {
    width: 1093px; height: 1200px; overflow: hidden;
    background: var(--backdrop);
    font-family: "Montserrat", sans-serif;
  }
  .card {
    position: absolute; left: 264px; width: 580px;
    box-shadow: 3px 3px 4px var(--shadow);
    overflow: hidden;
  }
  /* Front */
  .card-front { top: 226px; height: 359px; background: var(--paper); }
  .scenery {
    position: absolute; left: 0; top: 0; width: 100%; height: 150px;
    background: linear-gradient(180deg, #000 0%, #1e1e1e 55%, #6a6a6a 100%);
  }
  .holder-name {
    position: absolute; top: 184px; width: 100%; text-align: center;
    font-weight: 700; font-size: 22px; letter-spacing: 0.3px; color: var(--ink);
  }
  .name-rule {
    position: absolute; top: 222px; left: 262px; width: 56px; height: 1px;
    background: var(--rule);
  }
  .contact-row {
    position: absolute; top: 242px; left: 33px; right: 20px;
    display: flex; align-items: center; gap: 28px;
  }
  .contact-item { display: flex; align-items: center; gap: 4px; }
  .contact-icon { width: 41px; height: 41px; flex: none; }
  .contact-text { font-weight: 500; font-size: 26px; color: var(--ink); white-space: nowrap; }
  .services-band {
    position: absolute; left: 0; bottom: 0; width: 100%; height: 48px;
    background: var(--ink); color: var(--paper);
    display: flex; align-items: center; justify-content: center; gap: 8px;
    font-weight: 600; font-size: 16.5px; letter-spacing: 0.2px;
  }
  .service-dot { width: 8px; height: 8px; border-radius: 50%; background: var(--teal); }
  /* Back */
  .card-back {
    top: 620px; height: 357px;
    background: linear-gradient(160deg, #000 0%, #000 45%, #151515 75%, #1c1c1c 100%);
  }
  .backdrop-scenery {
    position: absolute; inset: 0;
    background: radial-gradient(ellipse at 85% 70%, rgba(40,40,40,0.6), rgba(0,0,0,0) 60%);
  }
  .brand-name {
    position: absolute; top: 130px; width: 100%; text-align: center;
    color: var(--paper); font-weight: 700; font-size: 36px; line-height: 1.25;
    letter-spacing: 2px; text-transform: uppercase;
  }
</style>
</head>
<body>
  <section class="card card-front">
    <div class="scenery" role="img" aria-label="Illustration of a white mountain peak flanked by pine trees on black"></div>
    <h1 class="holder-name">COLIN VANDRO</h1>
    <div class="name-rule"></div>
    <div class="contact-row">
      <div class="contact-item">
        <svg class="contact-icon" viewBox="0 0 40 40" aria-hidden="true">
          <circle cx="20" cy="20" r="18.5" fill="none" stroke="var(--teal)" stroke-width="1.6"/>
          <path d="M14 11c1.5-1 2.5-.5 3.3 1l1.5 3c.5 1 0 1.8-.8 2.4l-1 .8c.8 2.3 2.6 4.2 4.8 5.3l.9-1c.7-.8 1.5-1.1 2.5-.5l2.8 1.7c1.3.8 1.6 1.9.5 3.2-1.4 1.700-3.2 2.2-5.3 1.3-5-2.1-8.6-6-10.4-11-.8-2.3-.3-4.5 1.2-6.2z" fill="none" stroke="var(--ink)" stroke-width="1.6" stroke-linejoin="round"/>
          <path d="M22 12a6 6 0 0 1 6 6M22 8.5a9.5 9.5 0 0 1 9.5 9.5" fill="none" stroke="var(--teal)" stroke-width="1.6" stroke-linecap="round"/>
        </svg>
        <span class="contact-text">555-214-0387</span>
      </div>
      <div class="contact-item">
        <svg class="contact-icon" viewBox="0 0 40 40" aria-hidden="true">
          <circle cx="20" cy="20" r="18.5" fill="none" stroke="var(--teal)" stroke-width="1.6"/>
          <path d="M20 33c-1-3-8-9-8-15a8 8 0 0 1 16 0c0 6-7 12-8 15z" fill="var(--teal)"/>
          <circle cx="20" cy="18" r="2.6" fill="var(--paper)"/>
        </svg>
        <span class="contact-text">Alderbrook, OH</span>
      </div>
    </div>
    <div class="services-band">
      <span>PUMPING</span><span class="service-dot"></span>
      <span>INSPECTIONS</span><span class="service-dot"></span>
      <span>INSTALLS</span><span class="service-dot"></span>
      <span>REPAIRS</span>
    </div>
  </section>

  <section class="card card-back">
    <div class="backdrop-scenery" role="img" aria-label="Faint dark mountain and pine silhouettes"></div>
    <h2 class="brand-name">Birchline<br>Septic Solutions</h2>
  </section>
</body>
</html>
```